Hunting club needs a new web design !

We need a new web design for our hunting club located in Poland, called "BORYNA". The club was founded in 1952. Colors that we would like to see in the project are the colors of the forest. The website should be built in such a way that all text elements can be changed to another language and can't be graphic.
"BORYNA" means - big, thick forest in which the game, small and big resides

Target Market(s)

hunters,

Industry/Entity Type

Hunting

Coding

Coded - Design and coding required

Number of Pages Required

5+ page

Font styles to use
Decorative

Colors

Designer to choose colors to be used in the design.

Requirements
Must have
• current date, calendar,
• must contain almost all materials from our current web page
• http://boryna-lasowiec.webnest.pl/
• new web address: borynalsw.pl
Nice to have
• current weather in three hunting regions that we allowed to hunt, or indicated by the visitor on the map placed on our web,
• actual phase of the moon, actual moon rising hour, actual moon set hour, actual sun rise hour, actual sun set hour, current weather in region (stalowa wola, poland)
• wood, forest, deers, boars,
Should not have
• mountain photos, modern look, white or bright backgrounds,

```html
<!DOCTYPE html>
<html lang="en">
<head>
<meta charset="utf-8">
<title>BORYNA – Hunting Club</title>
<link rel="stylesheet" href="https://fonts.googleapis.com/css2?family=Montserrat:wght@400;600;700&family=Open+Sans:wght@400;600;700&family=Raleway:wght@400;500&display=swap">
<style>
:root{
  --olive:#4a3f10;
  --olive-text:#4b4a0c;
  --green:#4f8d12;
  --green-light:#6aae1e;
  --wood:#2a1d14;
  --wood-dark:#110b07;
  --blue:#2e69ad;
  --blue-dark:#23407a;
  --grey:#666;
  --line:#ddd;
  --white:#fff;
}
*{margin:0;padding:0;box-sizing:border-box}
html,body{width:1200px;height:3000px;overflow:hidden;background:var(--white)}
body{position:relative;font-family:"Open Sans",sans-serif;color:#333}
.abs{position:absolute}

/* header */
.brand{left:100px;top:24px;display:flex;align-items:center;gap:12px;font-family:"Montserrat",sans-serif;font-weight:700;font-size:30px;color:var(--green-light)}
.brand-dot{width:40px;height:40px;border-radius:50%;background:var(--green-light)}
.main-nav{top:50px;left:760px;display:flex;gap:56px;font-family:"Montserrat",sans-serif;font-size:15px;font-weight:600;color:#222}
.sub-nav{top:126px;left:0;width:1200px;height:60px;background:var(--olive);display:flex;align-items:center;justify-content:space-between;padding:0 100px;font-size:14px;font-weight:600;color:var(--white)}

/* hero */
.hero{top:186px;left:0;width:1200px;height:380px;background:linear-gradient(180deg,#3d5a2a 0%,#6f8f3f 35%,#4a6b2c 70%,#2f4a1c 100%)}
.hero-title{top:300px;left:0;width:1200px;text-align:center;font-family:"Montserrat",sans-serif;font-weight:700;font-size:46px;color:var(--white);letter-spacing:1px}
.hero-sub{top:390px;left:0;width:1200px;text-align:center;font-size:16px;color:var(--white)}
.hero-arrow{top:366px}
.weather-band{top:552px;left:0}
.wb-title{left:100px;top:578px;font-family:"Montserrat",sans-serif;font-weight:700;font-size:22px;line-height:34px;color:var(--white)}
.wb-div{top:584px;width:1px;height:86px;background:rgba(255,255,255,.6)}
.wb-temp{left:420px;top:584px;display:flex;align-items:center;gap:14px;color:var(--white);font-family:"Montserrat",sans-serif}
.wb-temp .deg{font-size:40px;font-weight:700}
.unit{font-size:15px;align-self:flex-start;margin-top:4px}
.wb-place{left:680px;top:592px;font-size:15px;line-height:28px;color:var(--white)}
.wb-stats{left:920px;top:592px;font-size:15px;line-height:24px;color:var(--white)}

/* welcome */
.calendar{left:100px;top:804px;width:366px;background:var(--white);box-shadow:0 4px 0 #e5e5e5,0 8px 0 #d8d8d8,0 3px 10px rgba(0,0,0,.2)}
.cal-head{height:56px;background:var(--green);display:flex;align-items:center;justify-content:space-between;padding:0 22px;color:var(--white);font-family:"Montserrat",sans-serif;font-weight:600;font-size:19px}
.cal-grid{display:grid;grid-template-columns:repeat(7,1fr)}
.cal-dow{height:36px;display:flex;align-items:center;justify-content:center;font-size:11px;color:#555}
.cal-day{height:52px;display:flex;align-items:center;justify-content:center;font-weight:700;font-size:14px;color:#222;border-top:1px solid var(--line);border-left:1px solid var(--line)}
.cal-day.muted{color:#999;font-weight:400}
.cal-day.today{background:var(--green);color:var(--white)}
.welcome{left:542px;top:798px;width:560px}
.sec-title{font-family:"Montserrat",sans-serif;font-weight:700;font-size:25px;color:var(--olive-text)}
.rule{height:2px;background:var(--olive-text);width:186px;margin-top:14px}
.welcome h3{font-weight:600;font-size:20px;color:#444;margin-top:38px}
.bullets{list-style:none;margin-top:26px}
.bullets li{display:flex;gap:14px;font-family:"Raleway",sans-serif;font-size:12.5px;line-height:22px;color:#666;margin-bottom:18px}
.bullets svg{flex:none;margin-top:3px}
.btn{display:inline-flex;align-items:center;justify-content:center;color:var(--white);font-family:"Montserrat",sans-serif;font-weight:600;font-size:15px}
.btn-green{background:var(--green)}
.btn-olive{background:var(--olive)}
.welcome .btn{width:140px;height:50px;margin-top:10px}

/* rise and set */
.wood{top:1270px;left:0}
.rs-title{top:1334px;left:0;width:1200px;text-align:center;font-family:"Montserrat",sans-serif;font-weight:700;font-size:26px;color:var(--white)}
.rs-rule{top:1392px;left:565px;width:70px;height:2px;background:rgba(255,255,255,.7)}
.tile{top:1462px;height:198px;border:2px solid #dfe6ef;background:linear-gradient(180deg,#3b7cc0,#25599a);color:var(--white);text-align:center;font-family:"Montserrat",sans-serif;box-shadow:0 4px 10px rgba(0,0,0,.5)}
.tile-head{height:58px;background:var(--blue-dark);display:flex;align-items:center;justify-content:center;font-size:14px;line-height:18px;padding:0 6px}
.tile-icon{height:64px;display:flex;align-items:center;justify-content:center}
.tile-value{font-size:20px;font-weight:600}
.tile-local .tile-head{font-size:17px}
.local-body{display:flex;align-items:center;justify-content:center;gap:10px;height:136px}
.local-body .big{font-size:62px;font-weight:400}

/* hunting places */
.hp-title{top:1876px;left:0;width:1200px;text-align:center}
.hp-rule{top:1932px;left:558px;width:84px;height:2px;background:var(--olive-text)}
.place{top:1988px;width:302px;text-align:center}
.place-img{height:188px;border-radius:20px 20px 40px 40px / 20px 20px 14px 14px;position:relative;box-shadow:0 3px 8px rgba(0,0,0,.25)}
.place-temp{position:absolute;left:62px;top:80px;display:flex;align-items:center;gap:14px;color:var(--white);font-family:"Montserrat",sans-serif}
.place-temp .deg{font-size:40px;font-weight:700}
.place h4{font-family:"Montserrat",sans-serif;font-weight:700;font-size:19px;margin-top:40px;color:#3a3a0a}
.place h4.green{color:var(--green)}
.place p{font-family:"Raleway",sans-serif;font-size:12.5px;line-height:20px;color:#333;margin-top:10px;padding:0 10px}
.place .btn{width:116px;height:42px;margin-top:22px;font-size:14px}

/* footer */
.footer{top:2466px;left:0}
.foot-brand{top:2540px;left:0;width:1200px;display:flex;justify-content:center;align-items:center;gap:12px;font-family:"Montserrat",sans-serif;font-weight:700;font-size:28px;color:var(--white)}
.foot-brand .dot{width:36px;height:36px;border-radius:50%;background:var(--white)}
.moon-title{top:2656px;left:0;width:1200px;text-align:center;font-family:"Montserrat",sans-serif;font-weight:700;font-size:23px;color:var(--white)}
.field{top:2722px;width:232px}
.field label{display:block;font-size:15px;color:var(--white);font-weight:600;margin-bottom:14px}
.select{height:44px;background:var(--white);display:flex;align-items:center;justify-content:space-between;padding:0 12px;font-size:14px;color:#333}
.moon-btn{top:2758px;left:856px;width:232px;height:46px;background:var(--green);border:2px solid #9ed05a;font-size:15px}
.foot-links{top:2858px;left:100px;width:1000px;display:flex;justify-content:space-between;font-family:"Montserrat",sans-serif;font-size:13px;font-weight:600;color:var(--white)}
.foot-line{top:2914px;left:100px;width:1000px;height:1px;background:rgba(255,255,255,.5)}
.copyright{top:2942px;left:100px;font-size:13px;color:var(--white)}
.social{top:2930px;left:876px;display:flex;gap:14px}
.social span{width:36px;height:36px;border-radius:50%;border:2px solid var(--white)}
</style>
</head>
<body>

<!-- header -->
<div class="abs brand"><span class="brand-dot"></span>BORYNA</div>
<nav class="abs main-nav"><span>KYNOLOGIA</span><span>NOWOSCI</span><span>GALERIA</span></nav>
<nav class="abs sub-nav">
  <span>Historia Kola</span><span>Zarzad Kola</span><span>Sklad Zarzadu</span><span>Uchwaly i Regulaminy</span><span>Urzadzenia Lowiecka</span><span>Plan Polowan</span><span>Kalendarz Polowan</span>
</nav>

<!-- hero -->
<div class="abs hero" role="img" aria-label="Sunlit forest with tall tree trunks"></div>
<h1 class="abs hero-title">BORYNA-LASOWIEC</h1>
<p class="abs hero-sub">We are a hunting club located in Poland, called "BORYNA". The club was founded in 1952.</p>
<svg class="abs hero-arrow" style="left:30px" width="36" height="60" viewBox="0 0 36 60"><path d="M30 4 L6 30 L30 56" fill="none" stroke="#fff" stroke-width="2"/></svg>
<svg class="abs hero-arrow" style="left:1134px" width="36" height="60" viewBox="0 0 36 60"><path d="M6 4 L30 30 L6 56" fill="none" stroke="#fff" stroke-width="2"/></svg>

<svg class="abs weather-band" width="1200" height="170" viewBox="0 0 1200 170">
  <defs><linearGradient id="band" x1="0" y1="0" x2="0" y2="1"><stop offset="0" stop-color="#3f7a14"/><stop offset="1" stop-color="#5a9a1c"/></linearGradient></defs>
  <path d="M0 0 H1200 V88 Q600 200 0 88 Z" fill="url(#band)"/>
</svg>
<div class="abs wb-title">WEATHER CONDITION<br>OF POLAND</div>
<div class="abs wb-div" style="left:386px"></div>
<div class="abs wb-temp">
  <svg width="40" height="40" viewBox="0 0 40 40"><circle cx="20" cy="20" r="19" fill="#fff"/><circle cx="20" cy="20" r="7" fill="none" stroke="#4f8d12" stroke-width="2.5"/><g stroke="#4f8d12" stroke-width="2.5"><path d="M20 6v4M20 30v4M6 20h4M30 20h4M10 10l3 3M27 27l3 3M30 10l-3 3M13 27l-3 3"/></g></svg>
  <span class="deg">29<sup style="font-size:22px">o</sup></span><span class="unit">°C | °F</span>
</div>
<div class="abs wb-div" style="left:644px"></div>
<div class="abs wb-place">Warsaw, Poland<br>Friday 2:00 PM, Sunny</div>
<div class="abs wb-div" style="left:884px"></div>
<div class="abs wb-stats">Precipitation: 0%<br>Humidity: 37%<br>Wind: 11km/h</div>

<!-- welcome -->
<div class="abs calendar">
  <div class="cal-head">
    <svg width="14" height="18" viewBox="0 0 14 18"><path d="M11 2 L4 9 L11 16" fill="none" stroke="#fff" stroke-width="3"/></svg>
    <span>July 16 2017</span>
    <svg width="14" height="18" viewBox="0 0 14 18"><path d="M3 2 L10 9 L3 16" fill="none" stroke="#fff" stroke-width="3"/></svg>
  </div>
  <div class="cal-grid">
    <div class="cal-dow">MON</div><div class="cal-dow">TUE</div><div class="cal-dow">WED</div><div class="cal-dow">THU</div><div class="cal-dow">FRI</div><div class="cal-dow">SAT</div><div class="cal-dow">SUN</div>
    <div class="cal-day muted">30</div><div class="cal-day">1</div><div class="cal-day">2</div><div class="cal-day">3</div><div class="cal-day">4</div><div class="cal-day">5</div><div class="cal-day">6</div>
    <div class="cal-day">7</div><div class="cal-day">8</div><div class="cal-day">9</div><div class="cal-day">10</div><div class="cal-day">11</div><div class="cal-day">12</div><div class="cal-day">13</div>
    <div class="cal-day">14</div><div class="cal-day">15</div><div class="cal-day today">16</div><div class="cal-day">17</div><div class="cal-day">18</div><div class="cal-day">19</div><div class="cal-day">20</div>
    <div class="cal-day">21</div><div class="cal-day">22</div><div class="cal-day">23</div><div class="cal-day">24</div><div class="cal-day">25</div><div class="cal-day">26</div><div class="cal-day">27</div>
    <div class="cal-day">28</div><div class="cal-day">29</div><div class="cal-day">30</div><div class="cal-day">31</div><div class="cal-day muted">1</div><div class="cal-day muted">2</div><div class="cal-day muted">3</div>
  </div>
</div>

<section class="abs welcome">
  <h2 class="sec-title">WELCOME TO BORYNA</h2>
  <div class="rule"></div>
  <h3>Nemo enim ipsam voluptatem quia voluptas</h3>
  <ul class="bullets">
    <li><svg width="16" height="16" viewBox="0 0 16 16"><circle cx="8" cy="8" r="7" fill="none" stroke="#4f8d12" stroke-width="2"/><path d="M5 8h6M8 5l3 3-3 3" fill="none" stroke="#4f8d12" stroke-width="2"/></svg><span>Nemo enim ipsam voluptatem quia voluptas sit aspernatur aut odit aut fugit, sed quia conse quuntur magni dolores eos qui ratione voluptatem sequi.</span></li>
    <li><svg width="16" height="16" viewBox="0 0 16 16"><circle cx="8" cy="8" r="7" fill="none" stroke="#4f8d12" stroke-width="2"/><path d="M5 8h6M8 5l3 3-3 3" fill="none" stroke="#4f8d12" stroke-width="2"/></svg><span>Nemo enim ipsam voluptatem quia voluptas sit aspernatur aut odit aut fugit, sed quia conse quuntur magni dolores eos qui ratione voluptatem sequi.</span></li>
    <li><svg width="16" height="16" viewBox="0 0 16 16"><circle cx="8" cy="8" r="7" fill="none" stroke="#4f8d12" stroke-width="2"/><path d="M5 8h6M8 5l3 3-3 3" fill="none" stroke="#4f8d12" stroke-width="2"/></svg><span>Nemo enim ipsam voluptatem quia voluptas sit aspernatur aut odit aut fugit, sed quia conse quuntur magni dolores eos qui ratione voluptatem sequi.</span></li>
  </ul>
  <span class="btn btn-green">Read More</span>
</section>

<!-- rise and set -->
<svg class="abs wood" width="1200" height="540" viewBox="0 0 1200 540" role="img" aria-label="Dark wood grain texture">
  <defs><radialGradient id="woodg" cx="0.5" cy="0.5" r="0.7"><stop offset="0" stop-color="#3a2a1e"/><stop offset="1" stop-color="#0d0805"/></radialGradient></defs>
  <path d="M0 70 Q600 -60 1200 70 V450 Q600 600 0 450 Z" fill="url(#woodg)"/>
</svg>
<h2 class="abs rs-title">RISE AND SET TIME</h2>
<div class="abs rs-rule"></div>

<div class="abs tile tile-local" style="left:100px;width:204px">
  <div class="tile-head">LOCAL WEATHER</div>
  <div class="local-body">
    <span class="big">16<sup style="font-size:26px">o</sup></span>
    <svg width="104" height="70" viewBox="0 0 104 70"><g fill="none" stroke="#fff" stroke-width="3"><circle cx="34" cy="30" r="14"/><path d="M34 4v8M34 48v8M8 30h8M10 12l6 6M58 12l-6 6M10 48l6-6"/><path d="M44 62h46a12 12 0 0 0 0-24 16 16 0 0 0-30-4 12 12 0 0 0-16 28z" fill="#2c62a4"/></g></svg>
  </div>
</div>
<div class="abs tile" style="left:314px;width:140px">
  <div class="tile-head">Actual phase of the moon</div>
  <div class="tile-icon"><svg width="40" height="40" viewBox="0 0 40 40"><circle cx="20" cy="20" r="17" fill="#fff"/><circle cx="14" cy="15" r="3" fill="#2c62a4"/><circle cx="25" cy="24" r="4" fill="#2c62a4"/><circle cx="14" cy="27" r="2" fill="#2c62a4"/></svg></div>
  <div class="tile-value" style="font-size:16px;line-height:20px">FULL MOON<br>PHASE</div>
</div>
<div class="abs tile" style="left:466px;width:140px">
  <div class="tile-head">Actual moon rising hour</div>
  <div class="tile-icon"><svg width="50" height="40" viewBox="0 0 50 40"><path d="M22 8a12 12 0 1 0 12 16 10 10 0 0 1-12-16z" fill="none" stroke="#fff" stroke-width="3"/><path d="M18 36h24a7 7 0 0 0 0-14 10 10 0 0 0-18 2 6 6 0 0 0-6 12z" fill="#2c62a4" stroke="#fff" stroke-width="3"/></svg></div>
  <div class="tile-value">10:20:30</div>
</div>
<div class="abs tile" style="left:614px;width:140px">
  <div class="tile-head">Actual moon set hour</div>
  <div class="tile-icon"><svg width="40" height="40" viewBox="0 0 40 40"><path d="M20 4a16 16 0 1 0 14 24 13 13 0 0 1-14-24z" fill="none" stroke="#fff" stroke-width="3"/><path d="M28 12l2 4 4 1-3 3 1 4-4-2-4 2 1-4-3-3 4-1z" fill="#fff"/></svg></div>
  <div class="tile-value">12:05:30</div>
</div>
<div class="abs tile" style="left:764px;width:140px">
  <div class="tile-head">Actual sun rise hour</div>
  <div class="tile-icon"><svg width="50" height="40" viewBox="0 0 50 40"><g fill="none" stroke="#fff" stroke-width="3"><path d="M13 30a12 12 0 0 1 24 0"/><path d="M4 34h42M25 4v8M9 14l5 5M41 14l-5 5M2 26h6M42 26h6"/></g></svg></div>
  <div class="tile-value">08:11:30</div>
</div>
<div class="abs tile" style="left:916px;width:140px">
  <div class="tile-head">Actual sun set hour</div>
  <div class="tile-icon"><svg width="50" height="40" viewBox="0 0 50 40"><g fill="none" stroke="#fff" stroke-width="3"><path d="M15 26a10 10 0 0 1 20 0"/><path d="M6 28h38M10 33q5-3 10 0t10 0 10 0M25 6v6M12 14l4 4M38 14l-4 4"/></g></svg></div>
  <div class="tile-value">09:20:30</div>
</div>

<!-- hunting places -->
<h2 class="abs sec-title hp-title">HUNTING PLACES</h2>
<div class="abs hp-rule"></div>

<div class="abs place" style="left:118px">
  <div class="place-img" role="img" aria-label="Misty green swamp forest" style="background:linear-gradient(180deg,#5d8a4a,#2f5a2a 70%,#3f7a20)">
    <div class="place-temp"><svg width="36" height="36" viewBox="0 0 40 40"><circle cx="20" cy="20" r="19" fill="#fff"/><circle cx="20" cy="20" r="7" fill="none" stroke="#4f8d12" stroke-width="2.5"/><g stroke="#4f8d12" stroke-width="2.5"><path d="M20 6v4M20 30v4M6 20h4M30 20h4M10 10l3 3M27 27l3 3M30 10l-3 3M13 27l-3 3"/></g></svg><span class="deg">29<sup style="font-size:20px">o</sup></span><span class="unit">°C | °F</span></div>
  </div>
  <h4>Nemo enim ipsam</h4>
  <p>Nemo enim ipsam voluptatem quia voluptas sit aspernatur aut odit aut fugit, sed quia consequn tur magni dolores eos qui.</p>
  <span class="btn btn-olive">Read More</span>
</div>
<div class="abs place" style="left:450px">
  <div class="place-img" role="img" aria-label="Green rolling meadow in warm light" style="background:linear-gradient(180deg,#9bb83a,#6a9a2a 50%,#4d7a1a)">
    <div class="place-temp"><svg width="36" height="36" viewBox="0 0 40 40"><circle cx="20" cy="20" r="19" fill="#fff"/><circle cx="20" cy="20" r="7" fill="none" stroke="#4f8d12" stroke-width="2.5"/><g stroke="#4f8d12" stroke-width="2.5"><path d="M20 6v4M20 30v4M6 20h4M30 20h4M10 10l3 3M27 27l3 3M30 10l-3 3M13 27l-3 3"/></g></svg><span class="deg">15<sup style="font-size:20px">o</sup></span><span class="unit">°C | °F</span></div>
  </div>
  <h4 class="green">Excepteur sint occaecat</h4>
  <p>Nemo enim ipsam voluptatem quia voluptas sit aspernatur aut odit aut fugit, sed quia consequn tur magni dolores eos qui.</p>
  <span class="btn btn-green">Read More</span>
</div>
<div class="abs place" style="left:784px">
  <div class="place-img" role="img" aria-label="Forest lake with trees on the shore" style="background:linear-gradient(180deg,#b8b48a,#4f6a2a 50%,#5a5a3a 75%,#3a4020)">
    <div class="place-temp"><svg width="36" height="36" viewBox="0 0 40 40"><circle cx="20" cy="20" r="19" fill="#fff"/><circle cx="20" cy="20" r="7" fill="none" stroke="#4f8d12" stroke-width="2.5"/><g stroke="#4f8d12" stroke-width="2.5"><path d="M20 6v4M20 30v4M6 20h4M30 20h4M10 10l3 3M27 27l3 3M30 10l-3 3M13 27l-3 3"/></g></svg><span class="deg">30<sup style="font-size:20px">o</sup></span><span class="unit">°C | °F</span></div>
  </div>
  <h4>Duis aute irure</h4>
  <p>Nemo enim ipsam voluptatem quia voluptas sit aspernatur aut odit aut fugit, sed quia consequn tur magni dolores eos qui.</p>
  <span class="btn btn-olive">Read More</span>
</div>

<!-- footer -->
<svg class="abs footer" width="1200" height="534" viewBox="0 0 1200 534" role="img" aria-label="Dark wood texture">
  <defs><linearGradient id="footg" x1="0" y1="0" x2="0" y2="1"><stop offset="0" stop-color="#3a2c1e"/><stop offset="1" stop-color="#1e160f"/></linearGradient></defs>
  <path d="M0 100 Q600 -100 1200 100 V534 H0 Z" fill="url(#footg)"/>
</svg>
<div class="abs foot-brand"><span class="dot"></span>BORYNA</div>
<h2 class="abs moon-title">FAZY KSIEZYCA</h2>
<div class="abs field" style="left:110px"><label>Rok:</label><div class="select">2014<svg width="10" height="6"><path d="M0 0h10L5 6z" fill="#333"/></svg></div></div>
<div class="abs field" style="left:358px"><label>Miesiac:</label><div class="select">Email<svg width="10" height="6"><path d="M0 0h10L5 6z" fill="#333"/></svg></div></div>
<div class="abs field" style="left:606px"><label>Dzien:</label><div class="select">Email<svg width="10" height="6"><path d="M0 0h10L5 6z" fill="#333"/></svg></div></div>
<span class="abs btn moon-btn">POKAZ FAZY KSIEZYCA</span>

<nav class="abs foot-links">
  <span>HISTORIA KOLA</span><span>|</span><span>ZARZAD KOLA</span><span>|</span><span>SKLAD ZARZADU</span><span>|</span><span>UCHWALY I REGULAMINY</span><span>|</span><span>URZADZENIA LOWIECKA</span><span>|</span><span>PLAN POLOWAN</span>
</nav>
<div class="abs foot-line"></div>
<p class="abs copyright">© Copyright 2017 boryna. All Right Reserved</p>
<div class="abs social"><span></span><span></span><span></span><span></span><span></span></div>

</body>
</html>
```